Redesign of the UI of a customer service platform

To improve the user experience of our customers, we need a new design for our agent interface of our customer service platform (velorant.com).
The focus will be on the dashboard and the inbox screens (see attached) along with the common UI elements (Buttons, menu, fonts, forms...)
We want a simple and distinctive design

Target Market(s)

Worldwide

Industry/Entity Type

It Service

Number of Pages Required

3 page

Font styles to use
Sans Serif

Requirements
Must have
• New Onboarding page: this is a new page that is shown to user the first time they login to the platform. This will replace the current onboarding screen (setup SMS, Setup widget...etc)
• Dashboard page: to access important information and activate services (see screenshot from current site)
• Inbox page: to manage all the interactions with customers. (see screenshot from current site)
• UI elements (buttons, menus, forms, tables, fonts, color palette)

```html
<!DOCTYPE html>
<html lang="en">
<head>
<meta charset="utf-8">
<title>Velorant Dashboard</title>
<link href="https://fonts.googleapis.com/css2?family=Open+Sans:wght@400;600&display=swap" rel="stylesheet">
<style>
:root{
  --blue:#2e8fc0;--green:#23a455;--coral:#ec7a6e;--teal:#3dd6c2;--sky:#5bbfea;
  --orange:#f7b500;--line:#e2e2e2;--text:#333;--muted:#777;--badge:#1e88e5;
}
*{box-sizing:border-box;margin:0;padding:0}
html,body{width:1200px;height:915px;overflow:hidden;background:#fff}
body{font-family:"Open Sans",sans-serif;color:var(--text)}
.stage{width:1400px;height:1067px;transform:scale(.857143);transform-origin:0 0;position:relative}
.abs{position:absolute}
.topbar{left:0;top:0;width:1400px;height:72px;border-bottom:1px solid var(--line)}
.brand-mark{left:26px;top:12px;width:48px;height:48px;border-radius:50%;background:#2b2b2b}
.nav{left:99px;top:0;display:flex;height:71px}
.nav-item{width:116px;border-left:1px solid var(--line);display:flex;flex-direction:column;align-items:center;justify-content:flex-end;padding-bottom:11px;font-size:12px;color:#444;position:relative}
.nav-item:last-child{border-right:1px solid var(--line)}
.nav-item.active{background:#f0f0f0}
.nav-item svg{width:16px;height:16px;margin-bottom:10px;fill:none;stroke:#888;stroke-width:1.5}
.count{position:absolute;left:83px;top:29px;width:26px;height:26px;border-radius:50%;color:#fff;font-size:12px;display:flex;align-items:center;justify-content:center}
.user{left:1218px;top:9px;display:flex;align-items:center;gap:10px;font-size:12px;color:#444}
.avatar{width:54px;height:54px;border-radius:50%;border:2px solid #3dc47e;background:linear-gradient(#c9a58a,#7a5a45);position:relative}
.avatar::after{content:"";position:absolute;left:-6px;top:0;width:11px;height:11px;border-radius:50%;background:#23c45e}
.title{font-size:30px;font-weight:400;color:var(--blue)}
.video{left:46px;top:202px;width:737px;height:485px;border:1px solid #ddd;background:#f3f3f3;padding:9px}
.video-photo{width:717px;height:465px;background:linear-gradient(120deg,#dfe8ec,#f5f7f7 45%,#cfd9dc);position:relative}
.play{left:312px;top:187px;width:92px;height:92px;border-radius:50%;background:#e74c4c;display:flex;align-items:center;justify-content:center}
.controls{left:6px;top:428px;width:704px;height:33px;display:flex;gap:8px}
.ctl-btn{width:55px;background:#3b3f3e;border-radius:3px;display:flex;align-items:center;justify-content:center}
.ctl-bar{flex:1;background:#3b3f3e;border-radius:3px;display:flex;align-items:center;padding:0 12px 0 8px;gap:10px;position:relative}
.track{flex:1;height:9px;border:1px solid #777}
.time{position:absolute;left:-6px;top:-6px;background:#eee;font-size:8px;padding:0 2px;color:#333}
.vol{width:28px;height:10px;background:repeating-linear-gradient(90deg,#38b7ef 0 2px,transparent 2px 4px)}
.clip{color:#fff;font-weight:600;font-size:14px}
.plan{left:817px;top:118px;width:537px;height:567px;border:1px solid #ddd;background:#fafafa}
.plan-head{height:50px;background:linear-gradient(#fff,#f0f0f0);border-bottom:1px solid #ddd;padding:11px 19px;font-size:20px;color:#333}
.plan-name{left:18px;top:68px;font-size:17px}
.btn-green{background:var(--green);color:#fff;font-size:13px;border-radius:2px;display:flex;align-items:center;gap:6px;justify-content:center}
.btn-green svg{width:11px;height:11px;fill:none;stroke:#fff;stroke-width:3}
.upgrade{left:412px;top:68px;width:95px;height:28px}
.tile{top:114px;width:141px;height:120px;border-radius:6px;color:#fff;text-align:center;font-size:15px;line-height:23px;padding-top:59px}
.tile svg{position:absolute;left:54px;top:20px;width:32px;height:32px;fill:#fff}
.tile .of{position:absolute;right:20px;top:13px;background:var(--badge);font-size:11px;line-height:19px;padding:0 8px;border-radius:2px}
.addon-list{left:22px;top:257px;width:481px}
.addon{height:86px;border:1px solid #ddd;border-left:5px solid var(--orange);background:#fff;margin-bottom:14px;padding:14px 17px;position:relative}
.addon.on{background:#e3f4fb}
.addon h3{font-size:17px;font-weight:400;margin-bottom:5px}
.addon p{font-size:13px;color:var(--muted)}
.addon .btn-green{position:absolute;right:18px;top:32px;width:81px;height:28px}
.scroll{left:517px;top:257px;width:6px;height:287px;border-radius:3px;background:#eee}
.scroll::after{content:"";position:absolute;left:0;top:38px;width:6px;height:52px;border-radius:3px;background:#ccc}
.sel{left:0;top:728px;width:1400px;text-align:center}
.cards{left:213px;top:813px;display:flex;gap:25px}
.card{width:175px;height:180px;border:1px solid #ddd;background:#f2f2f2;text-align:center;position:relative;padding-top:38px}
.card svg.icon{width:54px;height:50px;fill:none;stroke:var(--coral);stroke-width:5}
.card h4{font-size:18px;font-weight:600;color:#555;margin-top:10px}
.card .watch{font-size:14px;color:#555;margin-top:6px;display:flex;align-items:center;justify-content:center;gap:6px}
.dot{width:14px;height:14px;border-radius:50%;background:#2ea3e0;display:inline-flex;align-items:center;justify-content:center}
.dot::after{content:"";border-left:5px solid #fff;border-top:3.5px solid transparent;border-bottom:3.5px solid transparent;margin-left:2px}
.check{position:absolute;left:9px;top:9px;width:27px;height:27px;border-radius:50%;background:var(--green);display:flex;align-items:center;justify-content:center}
.footer{left:0;top:1033px;width:1400px;height:34px;background:#f5f5f5;border-top:1px solid var(--line);text-align:center;font-size:12px;line-height:34px;color:#444}
</style>
</head>
<body>
<div class="stage">
  <header class="topbar abs">
    <div class="brand-mark abs" role="img" aria-label="Velorant support agent mark"></div>
    <nav class="nav abs">
      <div class="nav-item active"><svg viewBox="0 0 16 16"><rect x="1.5" y="3" width="13" height="10"/><path d="M1.5 3l6.5 6 6.5-6"/></svg>INBOX<span class="count" style="background:#2cc185">4</span></div>
      <div class="nav-item"><svg viewBox="0 0 16 16"><path d="M3 1h7l3 3v11H3z M5 7h6M5 10h6"/></svg>TASKS<span class="count" style="background:#4aa8e0">4</span></div>
      <div class="nav-item"><svg viewBox="0 0 16 16" style="fill:#888;stroke:none"><circle cx="8" cy="5" r="3.5"/><path d="M2 15c0-4 2.5-6 6-6s6 2 6 6z"/></svg>CUSTOMERS</div>
      <div class="nav-item"><svg viewBox="0 0 16 16"><path d="M15 1L1 7l5 2 2 6z M6 9l9-8"/></svg>CAMPAIGNS</div>
      <div class="nav-item"><svg viewBox="0 0 16 16"><rect x="1" y="3" width="14" height="10"/><path d="M1 6h14"/></svg>PAYMENTS</div>
      <div class="nav-item"><svg viewBox="0 0 16 16"><path d="M1 1v14h14M4 12V8M7 12V5M10 12V7M13 12V3"/></svg>REPORTS</div>
      <div class="nav-item"><svg viewBox="0 0 16 16"><circle cx="8" cy="8" r="2.5"/><circle cx="8" cy="8" r="5.5" stroke-dasharray="2.5 1.8" stroke-width="3"/></svg>SETTINGS</div>
    </nav>
    <div class="user abs"><div class="avatar" role="img" aria-label="Agent profile photo"></div>MARCUS ELLERY</div>
  </header>

  <h1 class="title abs" style="left:48px;top:128px">Velorant Videos</h1>
  <div class="video abs">
    <div class="video-photo" role="img" aria-label="Video still of a smiling businessman at an office desk">
      <div class="play abs"><svg width="34" height="40" viewBox="0 0 34 40"><path d="M2 2l30 18-30 18z" fill="#fff"/></svg></div>
      <div class="controls abs">
        <div class="ctl-btn"><svg width="14" height="16" viewBox="0 0 14 16"><path d="M0 0l14 8-14 8z" fill="#fff"/></svg></div>
        <div class="ctl-bar"><span class="time">02:12</span><div class="track"></div><div class="vol"></div><span class="clip">clipvue</span></div>
      </div>
    </div>
  </div>

  <section class="plan abs">
    <div class="plan-head">Plan &amp; Add-ons</div>
    <div class="plan-name abs">Plan (Pro)</div>
    <div class="btn-green upgrade abs"><svg viewBox="0 0 12 12"><path d="M1 6l3.5 3.5L11 2"/></svg>Upgrade</div>
    <div class="tile abs" style="left:28px;background:var(--coral);border:1px solid #d9655c"><svg viewBox="0 0 32 32"><circle cx="16" cy="9" r="5"/><circle cx="7" cy="12" r="3.5"/><circle cx="25" cy="12" r="3.5"/><path d="M8 28c0-6 3-10 8-10s8 4 8 10z M1 26c0-5 2-8 6-8l2 1c-2 2-3 5-3 7z M31 26c0-5-2-8-6-8l-2 1c2 2 3 5 3 7z"/></svg><span class="of">1/1</span>Agents<br>Unlimited</div>
    <div class="tile abs" style="left:198px;background:var(--teal)"><svg viewBox="0 0 32 32"><path d="M11 8V5h10v3h8v20H3V8z M13 8h6V7h-6z" fill-rule="evenodd"/></svg><span class="of">1/1</span>Departments<br>Unlimed</div>
    <div class="tile abs" style="left:368px;background:var(--sky)"><svg viewBox="0 0 32 32"><path d="M8 3l5 6-3 3c1 4 5 8 9 10l3-3 6 5-3 4C14 27 4 17 4 7z"/></svg><span class="of">1/1</span>Phone<br>Unlimited</div>
    <div class="addon-list abs">
      <div class="addon"><h3>Phone + SMS</h3><p>Lorem Ipsum is simply dummy text of the printing</p></div>
      <div class="addon on"><h3>Chargevale</h3><p>Lorem Ipsum is simply dummy text of the printing</p><div class="btn-green"><svg viewBox="0 0 12 12"><path d="M1 6l3.5 3.5L11 2"/></svg>Active</div></div>
      <div class="addon"><h3>Relaygram</h3><p>Lorem Ipsum is simply dummy text of the printing</p><div class="btn-green"><svg viewBox="0 0 12 12"><path d="M1 6l3.5 3.5L11 2"/></svg>Active</div></div>
    </div>
    <div class="scroll abs"></div>
  </section>

  <h2 class="title sel abs">Select your Add-ons</h2>
  <div class="cards abs">
    <div class="card"><span class="check"><svg width="13" height="13" viewBox="0 0 12 12"><path d="M1 6l3.5 3.5L11 2" fill="none" stroke="#fff" stroke-width="2.5"/></svg></span><svg class="icon" viewBox="0 0 54 50"><rect x="4" y="4" width="46" height="30" rx="3"/><path d="M27 34v8M16 45h22"/></svg><h4>Widget</h4><div class="watch"><span class="dot"></span>Watch video</div></div>
    <div class="card"><svg class="icon" viewBox="0 0 54 50"><path d="M10 6h34v26H24l-10 9v-9h-4z"/></svg><h4>Chatlink</h4><div class="watch"><span class="dot"></span>Watch video</div></div>
    <div class="card"><svg class="icon" viewBox="0 0 54 50"><ellipse cx="22" cy="18" rx="18" ry="12"/><path d="M36 26c8 1 14 5 14 10s-3 6-5 7l2 5-8-4"/><path d="M10 28l-4 8 10-5"/></svg><h4>Sms</h4><div class="watch"><span class="dot"></span>Watch video</div></div>
    <div class="card"><svg class="icon" viewBox="0 0 54 50"><rect x="10" y="6" width="34" height="34" rx="2"/></svg><h4>Relaygram</h4><div class="watch"><span class="dot"></span>Watch video</div></div>
    <div class="card"><svg class="icon" viewBox="0 0 54 50"><path d="M37 14c-2-4-6-6-10-6-6 0-10 3-10 8 0 11 21 6 21 17 0 5-5 8-11 8-5 0-9-2-11-6M27 2v46"/></svg><h4>Payment</h4><div class="watch"><span class="dot"></span>Watch video</div></div>
  </div>

  <footer class="footer abs">Copyrights 2017. Velorant. All rights reserved.</footer>
</div>
</body>
</html>
```